Garlic Farm for Farm Sales/Restaurant sales

Need a professional, but appealing to agriculture world. We are selling 27 kinds of Organic Garlic from a farm in Simla,CO. I have uploaded logo and business information-we are going to need a template, because I will need to use it for four separate people.
-We are trying to appeal to Farm to table restaurants
-As well as growers/farmers

Target Market(s)

Agriculture Sales/Restaurants-Organic

Industry/Entity Type

Agriculture

Contact Information for Business Card

Want it to look more unique then your average kelto stock card- I want it to look amazing

Font styles to use
Sans Serif

Colors
0455a3
ec1f27
fbed22
ffffff

Requirements
Must have
• Just be creative
Nice to have
• Colorful
Should not have
• plain

```html
<!DOCTYPE html>
<html lang="en">
<head>
<meta charset="utf-8">
<title>Ridgeline Garlic – Business Card</title>
<link href="https://fonts.googleapis.com/css2?family=Roboto:wght@400;500;700&display=swap" rel="stylesheet">
<style>
  :root {
    --navy: #1f3a8a;
    --blue: #26449a;
    --red: #ec1f27;
    --yellow: #fbed22;
    --back-yellow: #c9b71a;
    --white: #ffffff;
    --ink: #111111;
    --stage: #2a2a2a;
  }
  html, body {
    margin: 0;
    width: 1200px;
    height: 903px;
    overflow: hidden;
    background: var(--stage);
    font-family: "Roboto", Arial, sans-serif;
  }
  .card {
    position: absolute;
    left: 320px;
    width: 560px;
    height: 320px;
    overflow: hidden;
    box-shadow: 0 8px 24px rgba(0,0,0,0.45);
  }
  .card-front { top: 100px; background: var(--white); }
  .card-back  { top: 480px; background: linear-gradient(135deg, #d6c41f, var(--back-yellow) 60%, #b3a214); }
  .card-shapes { position: absolute; inset: 0; }

  .holder {
    position: absolute;
    right: 34px;
    top: 22px;
    text-align: right;
  }
  .holder-name { font-size: 28px; font-weight: 700; color: var(--ink); line-height: 1.1; }
  .holder-role { font-size: 16px; font-weight: 500; color: var(--navy); }

  .contact {
    position: absolute;
    right: 24px;
    top: 122px;
    text-align: right;
    color: var(--white);
    font-size: 13px;
    line-height: 1.45;
  }
  .contact-ids { margin-bottom: 14px; }
  .contact-row { display: flex; justify-content: flex-end; align-items: center; gap: 8px; }
  .contact-icon { width: 11px; height: 11px; flex: none; }
  .contact-row .spacer { width: 11px; flex: none; }

  .brand-front {
    position: absolute;
    left: 40px;
    top: 168px;
    width: 190px;
    display: flex;
    align-items: center;
    gap: 12px;
  }
  .brand-dot { width: 30px; height: 30px; border-radius: 50%; background: var(--red); flex: none; }
  .brand-name { color: var(--navy); font-weight: 700; font-size: 22px; letter-spacing: 0.5px; line-height: 1.15; }

  .brand-back {
    position: absolute;
    inset: 0;
    display: flex;
    align-items: center;
    justify-content: center;
    gap: 16px;
  }
  .brand-back .brand-dot { width: 54px; height: 54px; }
  .brand-back .brand-name { font-size: 46px; }
</style>
</head>
<body>

<section class="card card-front" aria-label="Business card front">
  <svg class="card-shapes" width="560" height="320" viewBox="0 0 560 320">
    <polygon points="0,80 272,124 250,320 0,320" fill="var(--yellow)"/>
    <polyline points="0,70 280,114" stroke="var(--navy)" stroke-width="4" fill="none"/>
    <polygon points="290,118 560,70 560,320 266,320" fill="var(--blue)"/>
  </svg>

  <div class="holder">
    <div class="holder-name">Dana Holt</div>
    <div class="holder-role">Managing Director</div>
  </div>

  <div class="contact">
    <div class="contact-ids">
      <div class="contact-row">Lic : 30485512<span class="spacer"></span></div>
      <div class="contact-row">ABN : 562190<span class="spacer"></span></div>
    </div>
    <div class="contact-row">021-555-0134
      <svg class="contact-icon" viewBox="0 0 12 12"><rect width="12" height="12" rx="2" fill="var(--white)"/><path d="M3.5 2.5l1.5 0 .6 2-1 .8a5 5 0 0 0 2.1 2.1l.8-1 2 .6v1.5a1 1 0 0 1-1 1A6 6 0 0 1 2.5 3.5a1 1 0 0 1 1-1z" fill="var(--blue)"/></svg>
    </div>
    <div class="contact-row">ridgelinegarlic.com
      <svg class="contact-icon" viewBox="0 0 12 12"><rect width="12" height="12" rx="2" fill="var(--white)"/><circle cx="6" cy="6" r="3.5" fill="none" stroke="var(--blue)" stroke-width="1"/></svg>
    </div>
    <div class="contact-row">dana@ridgelinegarlic.com
      <svg class="contact-icon" viewBox="0 0 12 12"><rect width="12" height="12" rx="2" fill="var(--white)"/><path d="M2.5 4h7v4.5h-7zM2.5 4l3.5 2.6L9.5 4" fill="none" stroke="var(--blue)" stroke-width="1"/></svg>
    </div>
    <div class="contact-row">ridgelinegarlic.com.au<span class="spacer"></span></div>
  </div>

  <div class="brand-front">
    <span class="brand-dot"></span>
    <span class="brand-name">RIDGELINE<br>GARLIC</span>
  </div>
</section>

<section class="card card-back" aria-label="Business card back">
  <div class="brand-back">
    <span class="brand-dot"></span>
    <span class="brand-name">Ridgeline Garlic</span>
  </div>
</section>

</body>
</html>
```